Website Redesign - We Need Your Magic!

Hello we are looking for you to help us re-design a high end and professional website for a high-end private school.

Here is the current site: http://www.ferndalecrest.com/

NOTE THIS IS DESIGN ONLY, NO CODING :)

The image they want to portray is that of high quality sports and education, in a creative "un-stiff" way.

Menu Bar: Horizontal

Look and Feel:

Site Colors: Dark green and a Gold yellow (logos are attached)

This site will represent a school so the look must be clean, bold, and classy. The site must have a very clean user interface, with things easily recognizable. Think simple.

The site should be visually appealing! If you come to me with templates, or a ton of text you will be out.

This site should be outside the box, we do not want boring, we do not want status quo. This site should instill excitement, innovation, and athletics.

So the main points again are:

1. High-end and classy look, with creative feel
2. Simple and clear navigation style
3. To cover the Junior and High School - Ferndale Crest College Schools

Think outside the box. We look forward to seeing what you come up with!!

Thank you for helping us create an amazing site for the school!

Industry/Entity Type

School

```html
<!DOCTYPE html>
<html lang="en">
<head>
<meta charset="utf-8">
<title>Ferndale Crest College</title>
<link href="https://fonts.googleapis.com/css2?family=Open+Sans:wght@400;600;700&family=Oswald:wght@500;600&display=swap" rel="stylesheet">
<style>
:root{
  --green:#1e6e2c;
  --green-dark:#0f4a1c;
  --green-mid:#2e8a3c;
  --yellow:#f3e600;
  --gold:#e8c900;
  --page:#e9ece9;
  --ink:#333;
  --muted:#666;
  --white:#fff;
}
*{box-sizing:border-box;margin:0;padding:0}
html,body{width:776px;height:1200px;overflow:hidden}
body{background:var(--page);font-family:"Open Sans",Arial,sans-serif;color:var(--ink);position:relative}
.header{position:absolute;top:0;left:0;width:776px;height:148px;background:var(--white)}
.header__band{position:absolute;left:0;top:0;width:200px;height:40px;background:linear-gradient(90deg,var(--yellow),var(--green-mid))}
.brand{position:absolute;left:262px;top:44px;width:136px;text-align:center}
.brand__mark{display:block;width:44px;height:44px;border-radius:50%;background:var(--green);margin:0 auto 6px}
.brand__name{font-weight:700;font-size:14px;color:var(--green);line-height:1.1}
.phone{position:absolute;right:24px;top:14px;display:flex;align-items:center;gap:6px;color:var(--green);font-size:17px;font-weight:600}
.phone small{font-size:12px;color:var(--gold);font-weight:600}
.nav{position:absolute;top:148px;left:0;width:776px;height:36px;background:var(--yellow);display:flex;align-items:center;padding-left:12px}
.nav a{font-family:"Oswald",sans-serif;font-size:12px;font-weight:600;color:var(--green-dark);text-decoration:none;padding:0 11px;height:36px;line-height:36px}
.nav a.is-active{background:var(--green);color:var(--white)}
.nav .nav__gap{width:150px}
.slider{position:absolute;top:184px;left:10px;width:756px;height:312px;background:linear-gradient(180deg,#b9c8b4 0%,#cfc59a 55%,#6f7d5a 100%)}
.slider__caption{position:absolute;left:0;bottom:0;width:100%;height:50px;background:rgba(0,0,0,.65);padding:8px 16px;color:var(--white)}
.slider__caption h2{font-size:14px;font-weight:600}
.slider__caption p{font-size:9px;opacity:.85;margin-top:3px}
.slider__arrow{position:absolute;top:130px;width:30px;height:30px;border-radius:50%;background:var(--white);display:flex;align-items:center;justify-content:center}
.slider__arrow--prev{left:-4px}.slider__arrow--next{right:-4px}
.section-title{font-family:"Oswald",sans-serif;font-weight:500;font-size:15px;color:var(--green-dark);border-bottom:2px solid var(--green);padding-bottom:3px;width:220px}
.welcome{position:absolute;top:508px;left:30px;width:716px}
.welcome__photo{position:absolute;top:30px;left:0;width:222px;height:128px;background:linear-gradient(160deg,#c9b98a,#2d5b30)}
.welcome__text{position:absolute;top:0;left:238px;width:478px;font-size:8.5px;line-height:1.5;color:var(--muted)}
.welcome__text p+p{margin-top:6px}
.cols{position:absolute;top:672px;left:30px;width:716px;height:168px}
.col{position:absolute;top:0}
.col--academics{left:0;width:222px}
.col--life{left:236px;width:214px}
.col__head{background:var(--green);color:var(--white);font-family:"Oswald",sans-serif;font-size:13px;padding:5px 10px}
.col__intro{font-size:8.5px;color:var(--muted);line-height:1.45;margin:7px 0}
.col ul{list-style:none}
.col li{font-size:9px;color:var(--ink);padding:4px 0 4px 16px;border-bottom:1px dotted #bbb;position:relative}
.col li svg{position:absolute;left:0;top:5px}
.social{position:absolute;left:464px;top:0;width:252px;height:162px;background:var(--white);border:1px solid #ccc;padding:6px 8px}
.social__title{font-size:9px;font-weight:700;color:var(--ink);border-bottom:1px solid #ddd;padding-bottom:4px}
.social__page{display:flex;align-items:center;gap:6px;margin-top:6px}
.social__thumb{width:28px;height:28px;background:var(--green)}
.social__name{font-size:10px;font-weight:700;color:var(--green)}
.social__like{font-size:8px;border:1px solid #aaa;background:#f4f4f4;padding:1px 5px;margin-top:2px;display:inline-block}
.social__count{font-size:8px;color:var(--muted);margin:6px 0 4px}
.social__grid{display:grid;grid-template-columns:repeat(8,1fr);gap:3px}
.social__grid span{height:26px;background:#8a8f86}
.social__grid span:nth-child(3n){background:#5d6a59}
.social__grid span:nth-child(4n){background:#a9a08a}
.events{position:absolute;top:850px;left:30px;width:716px}
.events__bar{height:26px;background:#dfe3df;display:flex;align-items:center;gap:8px;padding-left:8px;font-family:"Oswald",sans-serif;font-size:13px;color:var(--green-dark)}
.events__list{position:absolute;top:30px;left:0;width:388px;height:152px;background:var(--green-dark);padding:6px 8px}
.event{display:flex;gap:10px;padding:6px 0;border-bottom:1px solid rgba(255,255,255,.15)}
.event:last-child{border:0}
.event__date{width:38px;height:36px;background:var(--white);text-align:center;flex:none}
.event__date b{display:block;background:var(--green);color:var(--white);font-size:8px;line-height:13px}
.event__date span{font-size:14px;font-weight:700;color:var(--green-dark);line-height:22px}
.event p{font-size:9px;color:var(--white);line-height:1.45}
.events__photo{position:absolute;top:30px;left:394px;width:322px;height:152px;background:linear-gradient(180deg,#7d7a66,#1f3d24)}
.events__caption{position:absolute;bottom:0;left:0;width:100%;background:rgba(0,0,0,.6);color:var(--yellow);font-family:"Oswald",sans-serif;font-size:13px;padding:5px 10px}
.partners{position:absolute;top:1044px;left:30px;width:716px;height:56px;display:flex;justify-content:space-around;align-items:center}
.partners span{width:110px;height:34px;border-radius:4px}
.partners span:nth-child(1){background:#2b54a0}
.partners span:nth-child(2){background:#c9302c}
.partners span:nth-child(3){background:#e3a21a;border-radius:50%;width:60px;height:42px}
.partners span:nth-child(4){background:#3a9a4a}
.footer{position:absolute;top:1110px;left:0;width:776px;height:90px;background:var(--green-dark);color:var(--white);padding:10px 30px;font-size:8.5px;line-height:1.8}
.footer a{color:var(--white);text-decoration:none}
.footer__brand{position:absolute;right:40px;top:10px;text-align:center;font-weight:700;font-size:10px;color:var(--yellow)}
.footer__brand i{display:block;width:36px;height:36px;border-radius:50%;background:var(--yellow);margin:0 auto 3px}
.footer__copy{position:absolute;bottom:6px;left:0;width:100%;text-align:center;font-size:8px;opacity:.8}
</style>
</head>
<body>
<header class="header">
  <div class="header__band" role="img" aria-label="Yellow and green decorative band"></div>
  <div class="brand"><span class="brand__mark"></span><span class="brand__name">Ferndale Crest College</span></div>
  <div class="phone">
    <svg width="16" height="16" viewBox="0 0 24 24"><path fill="#1e6e2c" d="M6.6 10.8a15 15 0 0 0 6.6 6.6l2.2-2.2a1 1 0 0 1 1-.25 11.4 11.4 0 0 0 3.6.57 1 1 0 0 1 1 1V20a1 1 0 0 1-1 1A17 17 0 0 1 3 4a1 1 0 0 1 1-1h3.5a1 1 0 0 1 1 1c0 1.25.2 2.45.57 3.57a1 1 0 0 1-.25 1z"/></svg>
    <small>Call:</small> 123 456 7890
  </div>
</header>
<nav class="nav">
  <a class="is-active" href="#">HOME</a><a href="#">ABOUT US</a><a href="#">ACADEMICS</a><a href="#">SPORTS</a>
  <span class="nav__gap"></span>
  <a href="#">JOINING</a><a href="#">COLLEGE WORK</a><a href="#">CONTACT US</a>
</nav>
<section class="slider" role="img" aria-label="Photo of the college main building with palm trees">
  <div class="slider__arrow slider__arrow--prev"><svg width="12" height="12" viewBox="0 0 12 12"><path d="M8 1 3 6l5 5" stroke="#333" stroke-width="2" fill="none"/></svg></div>
  <div class="slider__arrow slider__arrow--next"><svg width="12" height="12" viewBox="0 0 12 12"><path d="m4 1 5 5-5 5" stroke="#333" stroke-width="2" fill="none"/></svg></div>
  <div class="slider__caption"><h2>Lorem ipsum dolor sit amet consectetur adipiscing elit</h2><p>Proin ornare augue purus, non cursus nibh vestibulum quis. Sed et nisi quis eros sagittis.</p></div>
</section>
<section class="welcome">
  <h2 class="section-title">WELCOME TO FCPS</h2>
  <div class="welcome__photo" role="img" aria-label="Photo of the college bus in front of the school"></div>
  <div class="welcome__text">
    <p>Lorem ipsum dolor sit amet, consectetur adipiscing elit. Proin eu accumsan justo. Nullam luctus sapien vitae mauris aliquet, in convallis dui fermentum. Integer non dolor ultricies, vehicula erat eu, sagittis leo. In porta vitae nisl vel malesuada. Nunc non ultrices velit, non pharetra diam. Nulla tate, gravida augue vitae, interdum arcu.</p>
    <p>Integer non urna consequat, sagittis ante ac, varius mi. Pellentesque convallis mi ac mauris nec dignissim vehicula. Aliquam egestas et velit eu mattis. Sed et facilisis mauris, vitae vestibulum lorem. Praesent iaculis, quam ut rutrum hendrerit, odio dolor pretium justo, ac eleifend urna mauris aliquet velit. Nullam laoreet sollicitudin est, at tincidunt turpis mollis eget.</p>
  </div>
</section>
<section class="cols">
  <div class="col col--academics">
    <h3 class="col__head">ACADEMICS</h3>
    <p class="col__intro">Lorem ipsum sit consectetuer adipiscing elit sed diam nonummy.</p>
    <ul>
      <li><svg width="10" height="10" viewBox="0 0 10 10"><path d="m1 5 3 3 5-6" stroke="#1e6e2c" stroke-width="2" fill="none"/></svg>Undergraduate Education</li>
      <li><svg width="10" height="10" viewBox="0 0 10 10"><path d="m1 5 3 3 5-6" stroke="#1e6e2c" stroke-width="2" fill="none"/></svg>Colleges &amp; Departments</li>
      <li><svg width="10" height="10" viewBox="0 0 10 10"><path d="m1 5 3 3 5-6" stroke="#1e6e2c" stroke-width="2" fill="none"/></svg>Graduate School</li>
      <li><svg width="10" height="10" viewBox="0 0 10 10"><path d="m1 5 3 3 5-6" stroke="#1e6e2c" stroke-width="2" fill="none"/></svg>Distance Learning</li>
    </ul>
  </div>
  <div class="col col--life">
    <h3 class="col__head">STUDENTS LIFE</h3>
    <p class="col__intro">Lorem ipsum sit consectetuer adipiscing elit sed diam nonummy.</p>
    <ul>
      <li><svg width="10" height="10" viewBox="0 0 10 10"><path d="m1 5 3 3 5-6" stroke="#1e6e2c" stroke-width="2" fill="none"/></svg>Clubs &amp; Organizations</li>
      <li><svg width="10" height="10" viewBox="0 0 10 10"><path d="m1 5 3 3 5-6" stroke="#1e6e2c" stroke-width="2" fill="none"/></svg>Living On and Off Campus</li>
      <li><svg width="10" height="10" viewBox="0 0 10 10"><path d="m1 5 3 3 5-6" stroke="#1e6e2c" stroke-width="2" fill="none"/></svg>Recreational Sports</li>
      <li><svg width="10" height="10" viewBox="0 0 10 10"><path d="m1 5 3 3 5-6" stroke="#1e6e2c" stroke-width="2" fill="none"/></svg>Photo Galleries</li>
    </ul>
  </div>
  <div class="social">
    <p class="social__title">Find us on Campus Social</p>
    <div class="social__page"><span class="social__thumb"></span><div><p class="social__name">Ferndale Crest</p><span class="social__like">Like</span></div></div>
    <p class="social__count">1,234 people like Ferndale Crest.</p>
    <div class="social__grid" role="img" aria-label="Grid of member profile photos">
      <span></span><span></span><span></span><span></span><span></span><span></span><span></span><span></span>
      <span></span><span></span><span></span><span></span><span></span><span></span><span></span><span></span>
    </div>
  </div>
</section>
<section class="events">
  <div class="events__bar"><svg width="14" height="14" viewBox="0 0 14 14"><circle cx="7" cy="7" r="6" fill="#1e6e2c"/></svg>UPCOMING EVENTS</div>
  <div class="events__list">
    <div class="event"><div class="event__date"><b>DEC</b><span>04</span></div><p>Lorem ipsum dolor sit amet, consectetuer adipiscing elit, sed diam nonummy nibh euismod</p></div>
    <div class="event"><div class="event__date"><b>DEC</b><span>04</span></div><p>Lorem ipsum dolor sit amet, consectetuer adipiscing elit, sed diam nonummy nibh euismod</p></div>
    <div class="event"><div class="event__date"><b>DEC</b><span>04</span></div><p>Lorem ipsum dolor sit amet, consectetuer adipiscing elit, sed diam nonummy nibh euismod</p></div>
  </div>
  <div class="events__photo" role="img" aria-label="Group photo of conference delegates">
    <div class="events__caption">NATIONAL COACHING CONFERENCE</div>
  </div>
</section>
<section class="partners" aria-label="Partners"><span></span><span></span><span></span><span></span></section>
<footer class="footer">
  <p><a href="#">Home</a> | <a href="#">About Us</a> | <a href="#">Academics</a> | <a href="#">Sports Joining</a> | <a href="#">College Work</a> | <a href="#">Contact Us</a></p>
  <p>Add: Ferndale Crest College, 12 Ridge Road, Greenvale, Private Bag 34</p>
  <p>Call: 0712 000 321 | 0712 000 456 &nbsp; Email: info@ferndalecrest.com</p>
  <div class="footer__brand"><i></i>Ferndale Crest</div>
  <p class="footer__copy">Copyright © 2014 Ferndale Crest College. All Rights Reserved</p>
</footer>
</body>
</html>
```